Small Business Broker Business Card Design

A business card design for a small business brokerage, which is a financial service, not unlike real estate brokerage, but for small businesses such as laundromats, pizza shops, restaurants, cleaners etc. The designs should all be simple, more conservative in nature, using the colors and font of the logo. Again, think real estate Brokerage as a business context
Contact Information for Business Card
Name: Glen R. Harlow. Title: Small Business Advisor. Email: g.harlow@bayfieldcapitalworks.example. Mobile: (555) 274-3918. Office: (555) 806-2147. www.bayfieldcapitalworks.example

```html
<!DOCTYPE html>
<html lang="en">
<head>
<meta charset="utf-8">
<title>Bayfield Capital Works – Business Card</title>
<link href="https://fonts.googleapis.com/css2?family=Montserrat:wght@500;700;800&family=Arimo:wght@400&display=swap" rel="stylesheet">
<style>
  :root {
    --navy-deep: #0f2858;
    --navy: #16336f;
    --navy-light: #1f4288;
    --green: #8dc63f;
    --white: #ffffff;
    --backdrop: #141518;
  }
  html, body {
    margin: 0;
    padding: 0;
    width: 1200px;
    height: 963px;
    overflow: hidden;
    background: var(--backdrop);
  }
  .sheet {
    width: 1200px;
    height: 963px;
    display: flex;
    flex-direction: column;
    align-items: center;
    justify-content: center;
    gap: 40px;
  }
  .card {
    position: relative;
    width: 735px;
    height: 420px;
    border-radius: 26px;
    overflow: hidden;
    box-sizing: border-box;
  }
  .card-front {
    background: linear-gradient(135deg, var(--navy-deep) 0%, var(--navy) 55%, var(--navy-light) 100%);
    padding: 46px 54px;
  }
  .company-name {
    font-family: "Montserrat", sans-serif;
    font-weight: 800;
    color: var(--white);
    text-transform: uppercase;
    letter-spacing: 2px;
    margin: 0;
  }
  .tagline {
    font-family: "Montserrat", sans-serif;
    font-weight: 700;
    color: var(--green);
    text-transform: uppercase;
    letter-spacing: 1.6px;
    margin: 3px 0 0;
  }
  .card-front .company-name { font-size: 24px; }
  .card-front .tagline { font-size: 11px; }
  .person { margin-top: 40px; }
  .person-name {
    font-family: "Montserrat", sans-serif;
    font-weight: 800;
    font-size: 27px;
    color: var(--white);
    text-transform: uppercase;
    letter-spacing: 1.5px;
    margin: 0;
  }
  .person-title {
    font-family: "Arimo", sans-serif;
    font-size: 17px;
    color: var(--green);
    margin: 4px 0 0;
  }
  .contact-list {
    list-style: none;
    margin: 30px 0 0;
    padding: 0;
    font-family: "Arimo", sans-serif;
    font-size: 15.5px;
    color: var(--white);
  }
  .contact-list li {
    display: flex;
    align-items: center;
    gap: 10px;
    margin-bottom: 7px;
  }
  .contact-list svg { width: 15px; height: 15px; flex: none; }
  .corner-rule {
    position: absolute;
    right: 0;
    bottom: 0;
    width: 300px;
    height: 10px;
    background: var(--green);
  }
  .card-back {
    display: flex;
    flex-direction: column;
    align-items: center;
    justify-content: center;
  }
  .back-texture {
    position: absolute;
    inset: 0;
    background: radial-gradient(ellipse at 40% 40%, var(--navy-light) 0%, var(--navy) 50%, var(--navy-deep) 100%);
  }
  .brand-lockup {
    position: relative;
    display: flex;
    align-items: center;
    gap: 18px;
  }
  .brand-square {
    width: 40px;
    height: 40px;
    background: var(--green);
  }
  .card-back .company-name { font-size: 28px; }
  .card-back .tagline { font-size: 12.5px; }
</style>
</head>
<body>
<main class="sheet">
  <section class="card card-front">
    <h1 class="company-name">Bayfield Capital Works, Inc</h1>
    <p class="tagline">Confidently buy or sell a local business today</p>
    <div class="person">
      <h2 class="person-name">Glen R. Harlow</h2>
      <p class="person-title">Small Business Advisor</p>
    </div>
    <ul class="contact-list">
      <li>
        <svg viewBox="0 0 16 16" aria-hidden="true"><path d="M3 1.5l3 .5 1 3.2-1.8 1.3a9 9 0 0 0 4.3 4.3l1.3-1.8 3.2 1 .5 3-2 1.5C6.5 14 2 9.5 1.5 3.5z" fill="#8dc63f"/></svg>
        (555) 806-2147
      </li>
      <li>
        <svg viewBox="0 0 16 16" aria-hidden="true"><rect x="4" y="1" width="8" height="14" rx="1.5" fill="none" stroke="#8dc63f" stroke-width="1.5"/><circle cx="8" cy="12.5" r=".9" fill="#8dc63f"/></svg>
        (555) 274-3918
      </li>
      <li>
        <svg viewBox="0 0 16 16" aria-hidden="true"><rect x="1.5" y="3.5" width="13" height="9" fill="none" stroke="#8dc63f" stroke-width="1.4"/><path d="M1.5 3.5L8 9l6.5-5.5" fill="none" stroke="#8dc63f" stroke-width="1.4"/></svg>
        g.harlow@bayfieldcapitalworks.example
      </li>
      <li>
        <svg viewBox="0 0 16 16" aria-hidden="true"><circle cx="8" cy="8" r="6.5" fill="none" stroke="#8dc63f" stroke-width="1.3"/><ellipse cx="8" cy="8" rx="3" ry="6.5" fill="none" stroke="#8dc63f" stroke-width="1.1"/><path d="M1.5 8h13M2.5 5h11M2.5 11h11" stroke="#8dc63f" stroke-width="1"/></svg>
        www.bayfieldcapitalworks.example
      </li>
    </ul>
    <div class="corner-rule"></div>
  </section>

  <section class="card card-back">
    <div class="back-texture" role="img" aria-label="Embossed repeating brand pattern on navy card stock"></div>
    <div class="brand-lockup">
      <div class="brand-square"></div>
      <div>
        <p class="company-name">Bayfield Capital Works, Inc</p>
        <p class="tagline">Confidently buy or sell a local business today</p>
      </div>
    </div>
  </section>
</main>
</body>
</html>
```